Bramwell Corner Sports Pub. Where the locals go!!

We are creating a sports pub. We are needing a fun website that offers our menu along with an event page and general info. We have some attached links that we really like:
https://www.dunmorrows.example/
https://www.cafepelindra.example/
https://www.quillstoneyx.example/
We are doing a pirate theme but that is because the area we are in. We would like to see a pirate like in our logo doing something like drinking real time similar to the dunmorrows website above.
Target Market(s)
Sports Fans
Industry/Entity Type
Pub, Bar, Restaurant
Coding
Coded - Design and coding required
Number of Pages Required
3 page
Font styles to use
Other font styles liked:
- see uploads
Look and feel

```html
<!DOCTYPE html>
<html lang="en">
<head>
<meta charset="utf-8">
<title>Bramwell Corner Sports Pub</title>
<link href="https://fonts.googleapis.com/css2?family=Rye&family=Poppins:wght@400;500;600;700&display=swap" rel="stylesheet">
<style>
:root{
  --tan:#dcb188;
  --tan-light:#e3b98f;
  --brown:#6e3f1c;
  --brown-dark:#4a2810;
  --red:#c41f27;
  --ink:#1a1a1a;
  --white:#ffffff;
  --black:#000000;
}
*{margin:0;padding:0;box-sizing:border-box}
html,body{width:1200px;height:4271px;overflow:hidden}
body{position:relative;background:var(--tan);font-family:'Poppins',sans-serif;color:var(--ink)}
.abs{position:absolute}
.display{font-family:'Rye',serif;letter-spacing:2px;font-weight:400}
.btn{position:absolute;background:var(--red);color:var(--white);font-weight:700;font-size:15px;display:flex;align-items:center;justify-content:center;border-radius:6px;text-transform:uppercase;text-decoration:none;box-shadow:0 3px 6px rgba(0,0,0,.25)}
.copy{font-size:15px;line-height:31px;color:#2a1a10}

/* header */
.site-header{position:absolute;top:0;left:0;width:1200px;height:88px;background:var(--tan-light);z-index:5}
.header-brand{position:absolute;top:0;left:0;width:445px;height:88px;background:var(--black);clip-path:polygon(0 0,100% 0,91% 100%,0 100%)}
.brand-name{position:absolute;left:130px;top:33px;color:var(--white);font-family:'Rye',serif;font-size:16px;letter-spacing:1px;display:flex;align-items:center;gap:10px;text-transform:uppercase}
.brand-dot{width:20px;height:20px;border-radius:50%;background:var(--red);flex:none}
.main-nav a{position:absolute;top:34px;color:var(--white);font-weight:600;font-size:15px;text-decoration:none}

/* hero */
.hero-photo{position:absolute;top:0;left:0;width:1200px;height:828px;background:linear-gradient(135deg,#3a2012 0%,#6a3a1c 35%,#2b170b 70%,#120905 100%);clip-path:polygon(0 0,100% 0,100% 88%,50% 100%,0 88%)}
.hero-edge{position:absolute;top:0;left:0}
.hero-title{position:absolute;left:110px;top:285px;color:var(--white);font-size:48px;line-height:54px;text-transform:uppercase}
.hero-text{position:absolute;left:113px;top:406px;width:520px;color:var(--white);font-size:13.5px;line-height:28.5px}
.dots{position:absolute;display:flex;gap:6px}
.dots span{width:20px;height:20px;border-radius:50%;background:var(--white)}
.dots span.on{background:var(--red)}

/* about */
.section-title{color:var(--brown);font-size:36px}
.about-ring{position:absolute;left:784px;top:934px;width:280px;height:280px;border-radius:50%;border:15px solid var(--brown);background:var(--white);padding:10px}
.about-photo{width:100%;height:100%;border-radius:50%;background:radial-gradient(circle,#c44b3a,#3d2a66 60%,#8a2d1f)}
.about-badge{position:absolute;left:725px;top:1057px;width:200px;height:200px;border-radius:50%;background:var(--white);box-shadow:0 4px 10px rgba(0,0,0,.3);display:flex;align-items:center;justify-content:center}
.about-badge span{width:60px;height:60px;border-radius:50%;background:var(--red)}

/* menu band */
.menu-band{position:absolute;top:0;left:0}
.menu-art{position:absolute;left:75px;top:1458px;width:541px;height:497px;border-radius:30px;background:radial-gradient(ellipse at center,#e6b98a 0%,#d9a56f 45%,#5fb7d0 75%,#3a86a3 100%)}
.menu-art-label{position:absolute;left:75px;top:1680px;width:541px;text-align:center;color:var(--brown);font-family:'Rye',serif;font-size:34px;letter-spacing:2px}
.specials{position:absolute;left:671px;top:1528px;width:476px;height:353px;border:3px solid var(--white);border-radius:8px}
.specials h3{position:absolute;top:26px;width:100%;text-align:center;color:var(--white);font-size:26px}
.special-row{position:absolute;left:34px;width:410px;display:flex;align-items:center;color:var(--white)}
.special-row .item{font-size:14px;width:130px}
.special-row .leader{flex:1;border-bottom:2px dotted var(--white);margin:0 20px 0 0;height:8px}
.special-row .price{font-weight:700;font-size:23px;width:70px;text-align:right}

/* events */
.event-photo{position:absolute;box-shadow:0 4px 10px rgba(0,0,0,.45)}
.ev-one{left:111px;top:2318px;width:499px;height:396px;background:linear-gradient(160deg,#4a6a3a,#2a1a14 45%,#7a4a30 80%,#3a2015)}
.ev-two{left:605px;top:2714px;width:499px;height:398px;background:linear-gradient(200deg,#a0201a,#5a1a10 40%,#c77a50 75%,#2a140b)}

/* contact */
.footer-bg{position:absolute;left:0;top:3516px;width:1200px;height:755px;background:var(--black)}
.reach{position:absolute;left:109px;top:3251px;width:976px;height:527px;border-radius:8px;background:linear-gradient(135deg,#7a4522,#6a3a1a 50%,#8a5428)}
.reach h2{position:absolute;top:38px;width:100%;text-align:center;color:var(--white);font-size:34px}
.field{position:absolute;background:var(--white);font-size:15px;color:#333;padding:0 32px;display:flex;align-items:center}
.field.area{align-items:flex-start;padding-top:18px}

/* footer */
.foot-brand{position:absolute;left:111px;top:3858px;color:var(--white);font-family:'Rye',serif;font-size:22px;display:flex;align-items:center;gap:12px;letter-spacing:1px}
.social{position:absolute;left:116px;top:3926px;display:flex;gap:8px}
.social span{width:26px;height:26px;background:var(--white);border-radius:5px}
.subscribe{position:absolute;left:113px;top:3977px;width:348px;height:45px;display:flex}
.subscribe .input{flex:1;background:var(--white);font-weight:600;font-size:15px;display:flex;align-items:center;padding-left:20px}
.subscribe .send{width:65px;background:var(--red);display:flex;align-items:center;justify-content:center}
.foot-head{position:absolute;top:3862px;color:var(--white);font-family:'Rye',serif;font-size:18px;letter-spacing:1px}
.foot-links a{position:absolute;left:611px;color:var(--white);text-decoration:none;font-size:15px}
.contact-item{position:absolute;left:871px;display:flex;gap:16px;color:var(--white);font-size:15px;line-height:20px}
.contact-item .ico{width:38px;height:34px;background:var(--white);border-radius:3px;display:flex;align-items:center;justify-content:center;flex:none}
.rule{position:absolute;left:108px;top:4212px;width:974px;height:1px;background:#bbb}
.copyright{position:absolute;top:4228px;width:1200px;text-align:center;color:var(--white);font-size:13.5px}
</style>
</head>
<body>

<header class="site-header">
  <div class="header-brand"></div>
  <div class="brand-name"><span class="brand-dot"></span>Bramwell Corner Sports</div>
  <nav class="main-nav">
    <a style="left:515px" href="#">Home</a>
    <a style="left:601px" href="#">About US</a>
    <a style="left:717px" href="#">Events</a>
    <a style="left:817px" href="#">Menu’s</a>
    <a style="left:916px" href="#">Contact Us</a>
  </nav>
</header>

<section class="hero">
  <div class="hero-photo" role="img" aria-label="Photo of the pub's long wooden bar with stools and TV screens"></div>
  <svg class="hero-edge" width="1200" height="840" viewBox="0 0 1200 840">
    <polyline points="0,729 600,828 1200,729" fill="none" stroke="#6e3f1c" stroke-width="6"/>
  </svg>
  <h1 class="hero-title display">Welcome to<br>Bramwell Corner</h1>
  <p class="hero-text">Lorem ipsum dolor sit amet, consectetur adipiscing elit, sed do eiusmod tempor incididunt ut labore et dolore magna aliqua. Ut enim ad minim veniam, quis nostrud exercitation ullamco laboris nisi ut aliquip ex ea commodo consequat</p>
  <a class="btn" href="#" style="left:113px;top:538px;width:157px;height:50px">Get Started</a>
  <div class="dots" style="left:563px;top:640px"><span></span><span class="on"></span><span></span></div>
</section>

<section class="about">
  <h2 class="section-title display abs" style="left:110px;top:925px">ABOUT US</h2>
  <p class="copy abs" style="left:111px;top:985px;width:500px">Lorem ipsum dolor sit amet, consectetur adipiscing elit, sed do eiusmod tempor incididunt ut labore et dolore magna aliqua. Ut enim ad minim veniam, quis nostrud exercitation ullamco laboris nisi ut aliquip ex ea commodo consequat. Duis aute irure dolor in reprehenderit in voluptate velit esse cillum dolore eu fugiat nulla pariatur.</p>
  <a class="btn" href="#" style="left:111px;top:1185px;width:134px;height:44px">Read More</a>
  <div class="about-ring"><div class="about-photo" role="img" aria-label="Photo of the colourful pub interior"></div></div>
  <div class="about-badge"><span></span></div>
</section>

<svg class="menu-band" width="1200" height="2040" viewBox="0 0 1200 2040">
  <polyline points="0,1420 600,1310 1200,1420" fill="none" stroke="#6e3f1c" stroke-width="5"/>
  <polygon points="0,1450 600,1325 1200,1450 1200,2035 0,2035" fill="#6e3f1c"/>
</svg>
<section class="menu">
  <div class="menu-art" role="img" aria-label="Illustration of a pirate scroll with anchor, ship, parrot and waves"></div>
  <div class="menu-art-label">OUR MENU’S</div>
  <div class="specials">
    <h3 class="display">SPECIALS</h3>
    <div class="special-row" style="top:100px"><span class="item">LOREM IPSUM</span><span class="leader"></span><span class="price">$250</span></div>
    <div class="special-row" style="top:151px"><span class="item">LOREM IPSUM</span><span class="leader"></span><span class="price">$350</span></div>
    <div class="special-row" style="top:202px"><span class="item">LOREM IPSUM</span><span class="leader"></span><span class="price">$400</span></div>
    <div class="special-row" style="top:253px"><span class="item">LOREM IPSUM</span><span class="leader"></span><span class="price">$500</span></div>
  </div>
  <a class="btn" href="#" style="left:848px;top:1922px;width:135px;height:42px">View More</a>
</section>

<section class="events">
  <h2 class="section-title display abs" style="left:0;width:1200px;text-align:center;top:2134px">EVENTS</h2>
  <p class="copy abs" style="left:60px;width:1080px;top:2198px;text-align:center">Lorem ipsum dolor sit amet, consectetur adipiscing elit, sed do eiusmod tempor incididunt ut labore et dolore magna aliqua.<br>Ut enim ad minim veniam, quis nostrud exercitation ullamco laboris nisi ut aliquip ex ea commodo consequat.</p>
  <div class="event-photo ev-one" role="img" aria-label="Photo of fans cheering at the bar during a game"></div>
  <p class="copy abs" style="left:643px;top:2346px;width:450px">Lorem ipsum dolor sit amet, consectetur adipiscing elit, sed do eiusmod tempor incididunt ut labore et dolore magna aliqua. Ut enim ad minim veniam, quis nostrud exercitation ullamco laboris nisi ut aliquip ex ea commodo consequat. Duis aute irure dolor in reprehenderit in voluptate velit esse cillum dolore eu fugiat nulla pariatur. Excepteur sint occaecat cupidatat non proident, sunt in culpa qui officia deserunt mollit anim id est laborum.</p>
  <a class="btn" href="#" style="left:643px;top:2643px;width:133px;height:42px">Book Event</a>
  <p class="copy abs" style="left:119px;top:2755px;width:450px">Lorem ipsum dolor sit amet, consectetur adipiscing elit, sed do eiusmod tempor incididunt ut labore et dolore magna aliqua. Ut enim ad minim veniam, quis nostrud exercitation ullamco laboris nisi ut aliquip ex ea commodo consequat. Duis aute irure dolor in reprehenderit in voluptate velit esse cillum dolore eu fugiat nulla pariatur. Excepteur sint occaecat cupidatat non proident, sunt in culpa qui officia deserunt mollit anim id est laborum.</p>
  <a class="btn" href="#" style="left:121px;top:3054px;width:133px;height:42px">Book Event</a>
  <div class="event-photo ev-two" role="img" aria-label="Photo of a crowded pub evening under red lights"></div>
  <div class="dots" style="left:569px;top:3147px;gap:5px">
    <span class="on" style="width:16px;height:16px;border:2px solid #555"></span>
    <span style="width:16px;height:16px;background:#222;border:2px solid #555"></span>
    <span class="on" style="width:16px;height:16px;border:2px solid #555"></span>
  </div>
</section>

<div class="footer-bg"></div>
<section class="reach">
  <h2 class="display">REACH OUT</h2>
  <div class="field" style="left:98px;top:114px;width:375px;height:62px">Name</div>
  <div class="field" style="left:491px;top:114px;width:373px;height:62px">Email*</div>
  <div class="field area" style="left:98px;top:192px;width:767px;height:207px">Message</div>
  <a class="btn" href="#" style="left:96px;top:431px;width:135px;height:41px">Submit</a>
</section>

<footer>
  <div class="foot-brand"><span class="brand-dot" style="width:24px;height:24px"></span>BRAMWELL CORNER SPORTS PUB</div>
  <div class="social" aria-label="Social links"><span></span><span></span><span></span><span></span></div>
  <div class="subscribe">
    <div class="input">Email Address</div>
    <div class="send"><svg width="32" height="22" viewBox="0 0 32 22"><rect x="1" y="1" width="30" height="20" fill="none" stroke="#fff" stroke-width="2"/><polyline points="1,1 16,12 31,1" fill="none" stroke="#fff" stroke-width="2"/></svg></div>
  </div>

  <div class="foot-head" style="left:611px">QUICK LINKS</div>
  <nav class="foot-links">
    <a style="top:3906px" href="#">Home</a>
    <a style="top:3947px" href="#">About Us</a>
    <a style="top:3989px" href="#">Events</a>
    <a style="top:4030px" href="#">Menu’s</a>
    <a style="top:4071px" href="#">Contact us</a>
  </nav>

  <div class="foot-head" style="left:871px">CONTACT US</div>
  <div class="contact-item" style="top:3912px">
    <span class="ico"><svg width="16" height="20" viewBox="0 0 16 20"><path d="M8 1a6 6 0 0 0-6 6c0 5 6 12 6 12s6-7 6-12a6 6 0 0 0-6-6z" fill="#111"/><circle cx="8" cy="7" r="2.3" fill="#fff"/></svg></span>
    <span>48 Harbour Lane<br>Suite 12, Bramwell 04721</span>
  </div>
  <div class="contact-item" style="top:3978px">
    <span class="ico"><svg width="18" height="18" viewBox="0 0 18 18"><path d="M4 1l3 4-2 2c1 2 3 4 5 5l2-2 4 3-2 3C8 16 2 10 1 3z" fill="#111"/></svg></span>
    <span style="line-height:34px">+1 555 014 2290</span>
  </div>
  <div class="contact-item" style="top:4030px">
    <span class="ico"><svg width="24" height="16" viewBox="0 0 24 16"><rect x="1" y="1" width="22" height="14" fill="none" stroke="#111" stroke-width="2"/><polyline points="1,1 12,9 23,1" fill="none" stroke="#111" stroke-width="2"/></svg></span>
    <span>info@bramwellcorner<br>pub.example</span>
  </div>
  <div class="contact-item" style="top:4090px">
    <span class="ico"><svg width="20" height="20" viewBox="0 0 20 20"><circle cx="10" cy="10" r="9" fill="#111"/><polyline points="10,4 10,10 14,12" fill="none" stroke="#fff" stroke-width="2"/></svg></span>
    <span style="line-height:25px;padding-top:4px">HOURS<br>Mon-Fri&nbsp;&nbsp;&nbsp;11am -6pm<br>Sat-Sun&nbsp;&nbsp;&nbsp;11am -11pm</span>
  </div>

  <div class="rule"></div>
  <p class="copyright">Copyright © 2023 bramwell corner sports pub. All Rights Reserved.</p>
</footer>

</body>
</html>
```